Kestrel HVAC Services - High end letter head, Quote Template & Invoice Template

Provide word documents for the below.
- Letterhead for emails & letters.
- Quote template (similar to the attached)
- Invoice template (similar to the attached)
Logo colours should be used.
Modern, bold, professional look.
Kestrel Logo - Vantor Specialist Dealer logo - Contact information

See attachments of previously used documents.

Target Market(s)

High end clients

Industry/Entity Type

Air Conditioning & Mechanical Ventilation (HVAC)

Font styles to use
Sans Serif
Other font styles liked:
• Arial Narrow or similar - Text similar to the KESTREL logo

Requirements
Must have
• Kestrel Logo - Vantor Specialist Dealer logo - Contact information
Nice to have
• Logo colours used throughout the documents
Should not have
• Bright colours, yellow, pink, green etc

```html
<!DOCTYPE html>
<html lang="en">
<head>
<meta charset="utf-8">
<title>Kestrel HVAC Services – Letterhead</title>
<link rel="stylesheet" href="https://fonts.googleapis.com/css2?family=Arimo:wght@400;700&family=Open+Sans:wght@400;600&display=swap">
<style>
  :root {
    --paper: #f7f6f4;
    --ink: #2e2e2e;
    --ink-soft: #4a4a4a;
    --logo-black: #000000;
    --logo-white: #ffffff;
    --brand-blue: #1f6fb8;
    --dealer-blue: #1aa0d8;
    --rule: #8a8a8a;
  }
  * { margin: 0; padding: 0; box-sizing: border-box; }
  html, body { width: 912px; height: 1200px; overflow: hidden; background: var(--paper); }
  .letterhead {
    position: relative;
    width: 912px;
    height: 1200px;
    background: var(--paper);
    font-family: "Arimo", Arial, sans-serif;
    color: var(--ink);
  }
  .brand-block {
    position: absolute;
    left: 49px; top: 0;
    width: 313px; height: 128px;
    background: var(--logo-black);
    display: flex; align-items: center; justify-content: center; gap: 12px;
  }
  .brand-block .brand-square { width: 18px; height: 18px; background: var(--logo-white); }
  .brand-block .brand-name {
    font-family: "Arimo", Arial, sans-serif;
    font-weight: 700; font-size: 22px;
    color: var(--logo-white);
    letter-spacing: 0.5px;
  }
  .contact-list {
    position: absolute;
    left: 611px; top: 40px;
    list-style: none;
    font-family: "Open Sans", Arial, sans-serif;
    font-size: 17px;
    line-height: 22px;
    color: var(--ink);
  }
  .contact-list li { display: flex; align-items: center; gap: 8px; }
  .contact-list svg { width: 13px; height: 13px; fill: var(--brand-blue); flex: none; }
  .salutation {
    position: absolute;
    left: 90px; top: 292px;
    font-size: 26px; font-weight: 400;
    color: var(--ink-soft);
  }
  .letter-body {
    position: absolute;
    left: 90px; top: 358px;
    width: 737px;
    font-size: 14.4px;
    line-height: 21.4px;
    text-align: justify;
    color: var(--ink-soft);
  }
  .letter-body p { margin-bottom: 21.4px; }
  .sign-off { position: absolute; left: 90px; top: 814px; font-size: 14.4px; color: var(--ink-soft); }
  .signature {
    position: absolute; left: 85px; top: 840px;
    width: 122px; height: 50px;
    background: linear-gradient(90deg, rgba(40,40,40,0.05), rgba(40,40,40,0.18), rgba(40,40,40,0.05));
    border-radius: 4px;
  }
  .signatory { position: absolute; left: 96px; top: 908px; }
  .signatory .name { font-size: 20px; color: var(--ink); }
  .signatory .role { font-size: 14px; color: var(--ink-soft); margin-top: 4px; }
  .footer-rule {
    position: absolute; left: 90px; top: 1110px;
    width: 541px; height: 1px; background: var(--rule);
  }
  .footer-details {
    position: absolute; left: 92px; top: 1124px;
    font-family: "Open Sans", Arial, sans-serif;
    font-size: 13px; color: var(--ink-soft);
  }
  .dealer-mark {
    position: absolute; left: 648px; top: 1106px;
    display: flex; align-items: center; gap: 8px;
  }
  .dealer-mark .dealer-square { width: 16px; height: 16px; background: var(--dealer-blue); }
  .dealer-mark .dealer-name {
    font-family: "Arimo", Arial, sans-serif;
    font-weight: 700; font-size: 15px;
    color: var(--dealer-blue);
  }
</style>
</head>
<body>
<main class="letterhead">
  <header>
    <div class="brand-block">
      <span class="brand-square"></span>
      <span class="brand-name">Kestrel HVAC Services</span>
    </div>
    <ul class="contact-list">
      <li><svg viewBox="0 0 16 16" aria-hidden="true"><path d="M3.6 1.2l2.3 2.6-1.2 1.9c.9 2 2.6 3.7 4.6 4.6l1.9-1.2 2.6 2.3-1.4 2.6C7 13.8 2.2 9 1 3z"/></svg>0412 555 087</li>
      <li><svg viewBox="0 0 16 16" aria-hidden="true"><path d="M1 3h14v10H1z M1 3l7 5 7-5" stroke="#f7f6f4" stroke-width="1"/></svg>office@kestrelhvac.com.au</li>
      <li><svg viewBox="0 0 16 16" aria-hidden="true"><circle cx="8" cy="8" r="7"/><path d="M1 8h14M8 1c3 3 3 11 0 14M8 1c-3 3-3 11 0 14" stroke="#f7f6f4" stroke-width="1" fill="none"/></svg>www.kestrelhvac.com.au</li>
    </ul>
  </header>

  <h1 class="salutation">Dear Mr. Hale,</h1>

  <section class="letter-body">
    <p>Lorem ipsum dolor sit amet, consectetur adipiscing elit. Donec orci purus, luctus vitae dignissim eu, iaculis sed purus. Vivamus faucibus, ipsum nec aliquet viverra, leo mauris condimentum ligula, sit amet sagittis enim ligula quis arcu. Nam egestas tortor id nisi porttitor mattis. In tortor ante, ultricies in suscipit a, tempus non massa. Vivamus et auctor mi. Fusce vel massa nulla. Phasellus nec eros mauris, et scelerisque orci.</p>
    <p>Donec malesuada orci vitae nulla accumsan porta a id massa. Quisque accumsan iaculis magna sit amet fringilla. Maecenas consequat, magna eget tincidunt semper, odio nibh rutrum mi, id feugiat ante nisi eu risus. Vestibulum nunc orci, rhoncus a placerat in, ultricies in mi. Cras mattis varius eros, vel fringilla nisi suscipit eget. Quisque scelerisque sagittis nulla at porttitor.</p>
    <p>Sed id augue vitae urna euismod commodo aliquet a quam. Pellentesque arcu velit, cursus et malesuada ut, consequat et diam. Nullam erat sem, rhoncus id ullamcorper vitae, rhoncus et arcu. In ultricies ultricies nulla, ut rutrum nisi iaculis at. Donec eu magna a metus ornare faucibus. Fusce aliquet faucibus ultricies. Morbi semper, est id tincidunt gravida, sem arcu adipiscing lacus, ac bibendum nulla leo eu purus. Quisque nec diam sed risus consectetur a ccumsan quis quis nibh. Vestibulum id purus lorem.</p>
    <p>It is a long established fact that a reader will be distracted by the readable content of a page when looking at its layout. The point of using Lorem Ipsum is that it has a more-or-less normal distribution of letters, as opposed to using 'Content here, content here', making it look like readable English. Many desktop publishing packages</p>
  </section>

  <p class="sign-off">Sincerely,</p>
  <div class="signature" role="img" aria-label="Handwritten signature"></div>
  <div class="signatory">
    <p class="name">Peter Hale</p>
    <p class="role">CEO/ Founder</p>
  </div>

  <footer>
    <div class="footer-rule"></div>
    <p class="footer-details">ABN: 57 304 921 118 | Licence No: 281946C | ARC No: AU63115</p>
    <div class="dealer-mark">
      <span class="dealer-square"></span>
      <span class="dealer-name">Vantor Specialist Dealer</span>
    </div>
  </footer>
</main>
</body>
</html>
```